Job application set/company logo

My resume, profile and project file need to be designed in a common, fresh business design, not too playful and colourful
Potentially a logo for my company called Silver Reed Consulting needs to be designed in a second step. My company is consulting in digitalization and business transformation.

```html
<!DOCTYPE html>
<html lang="en">
<head>
<meta charset="utf-8">
<title>Marcus Thalberg – Resume</title>
<link rel="stylesheet" href="https://fonts.googleapis.com/css2?family=Poppins:wght@300;400;500;600;700&family=Libre+Baskerville:wght@700&display=swap">
<style>
:root{
  --bg:#ececec;
  --paper:#ffffff;
  --panel:#232323;
  --ink:#222222;
  --banner:#777777;
  --date:#e2e2e2;
  --band:#efefef;
  --fold:#8c8c8c;
}
*{margin:0;padding:0;box-sizing:border-box}
html,body{width:746px;height:1200px;overflow:hidden;background:var(--bg)}
body{position:relative;font-family:"Poppins",sans-serif;color:var(--ink)}
.page{position:absolute;left:170px;width:628px;height:886px;background:var(--paper);transform:scale(.645);transform-origin:0 0;box-shadow:0 2px 14px rgba(0,0,0,.14)}
.page-one{top:22px}
.page-two{top:609px}
.page > *{position:absolute}
.shape{left:0;top:0;width:628px;height:886px}
.name{left:32px;width:223px;top:222px;text-align:center;font-family:"Libre Baskerville",serif;font-weight:700;font-size:15.5px;color:#fff;letter-spacing:-.2px}
.role{left:32px;width:223px;top:245px;text-align:center;font-size:8px;line-height:10px;color:#e8e8e8}
.divider{height:1px;background:#8a8a8a}
.contact{left:79px;font-size:7.2px;line-height:9.5px;color:#fff}
.contact-icon{left:62px;width:11px;height:11px}
.side-title{width:223px;text-align:center;color:#fff;font-size:13px;font-weight:500;letter-spacing:.3px}
.side-line{left:61px;width:1px;background:#8a8a8a}
.side-head{left:68px;color:#fff;font-size:8.6px;font-weight:600}
.side-head::before{content:"";position:absolute;left:-9px;top:3px;width:5px;height:5px;border-radius:50%;background:#bdbdbd}
.side-item{left:79px;width:170px;color:#f0f0f0;font-size:7.3px;line-height:9.6px}
.side-item::before{content:"";position:absolute;left:-9px;top:2px;width:5px;height:5px;border-radius:50%;border:1px solid #fff;background:var(--panel)}
.side-text{left:76px;width:160px;color:#f0f0f0;font-size:7.3px;line-height:9.6px}
.banner{width:298px;height:26px;background:var(--banner);color:#fff;font-size:11.5px;font-weight:500;text-align:center;line-height:26px;border-radius:5px 5px 0 0;letter-spacing:.3px}
.banner .light{font-weight:300}
.timeline{width:1px;background:#9a9a9a}
.r-head{font-size:8.6px;font-weight:600;color:var(--ink)}
.r-head.dot::before{content:"";position:absolute;left:-13px;top:3px;width:5px;height:5px;border-radius:50%;background:#777}
.r-sub{font-size:8px;font-weight:600;line-height:10px;color:var(--ink)}
.r-item{font-size:7.3px;line-height:9.6px;color:#333}
.r-item::before{content:"";position:absolute;left:-9px;top:2px;width:5px;height:5px;border-radius:50%;background:#333}
.job{display:flex;justify-content:space-between;align-items:flex-start;font-size:8px;font-weight:600;line-height:10px}
.date{background:var(--date);padding:1px 7px;font-size:7.8px;font-weight:600;line-height:10px;white-space:nowrap}
.band{left:0;top:595px;width:628px;height:275px;background:var(--band)}
</style>
</head>
<body>

<main class="page page-one">
  <svg class="shape" viewBox="0 0 628 886" aria-hidden="true">
    <defs>
      <linearGradient id="portrait" x1="0" y1="0" x2="0" y2="1">
        <stop offset="0" stop-color="#d9d4cf"/>
        <stop offset=".5" stop-color="#8d7f74"/>
        <stop offset="1" stop-color="#2c2c30"/>
      </linearGradient>
    </defs>
    <path d="M32,162 Q32,139 55,139 H232 Q255,139 255,162 V764 L176,859 H55 Q32,859 32,836 Z" fill="#232323"/>
    <path d="M255,764 C246,800 214,832 176,859 C196,826 205,808 212,790 C224,784 240,776 255,764 Z" fill="#8c8c8c" role="img" aria-label="Folded page corner"/>
    <circle cx="144" cy="119" r="86" fill="#fff" stroke="#6e6e6e" stroke-width="6"/>
    <circle cx="144" cy="119" r="76" fill="url(#portrait)" role="img" aria-label="Portrait photo of the applicant"/>
  </svg>

  <div class="name">MARCUS THALBERG</div>
  <div class="role">Senior Advisor to Tech Industry<br>Digital Transformer</div>
  <div class="divider" style="left:84px;top:276px;width:120px"></div>

  <svg class="contact-icon" style="top:300px" viewBox="0 0 11 11" aria-hidden="true"><rect width="11" height="11" rx="2" fill="#cfcfcf"/><rect x="2" y="3" width="7" height="5" fill="none" stroke="#232323" stroke-width=".9"/><path d="M2,3 L5.5,6 L9,3" fill="none" stroke="#232323" stroke-width=".9"/></svg>
  <div class="contact" style="top:300px">m.thalberg@mailbox.example</div>
  <svg class="contact-icon" style="top:315px" viewBox="0 0 11 11" aria-hidden="true"><rect width="11" height="11" rx="2" fill="#cfcfcf"/><path d="M5.5,9.5 C3,6.5 3,5.5 3,4.5 A2.5,2.5 0 0 1 8,4.5 C8,5.5 8,6.5 5.5,9.5 Z" fill="#232323"/><circle cx="5.5" cy="4.5" r="1" fill="#cfcfcf"/></svg>
  <div class="contact" style="top:312px">Lindenweg 12<br>50667 Cologne, Germany</div>
  <svg class="contact-icon" style="top:344px" viewBox="0 0 11 11" aria-hidden="true"><rect width="11" height="11" rx="2" fill="#cfcfcf"/><rect x="2.5" y="3" width="6" height="5.5" fill="none" stroke="#232323" stroke-width=".9"/><line x1="2.5" y1="4.8" x2="8.5" y2="4.8" stroke="#232323" stroke-width=".9"/></svg>
  <div class="contact" style="top:345px">11.03.1968</div>
  <svg class="contact-icon" style="top:364px" viewBox="0 0 11 11" aria-hidden="true"><rect width="11" height="11" rx="2" fill="#cfcfcf"/><rect x="3" y="3" width="5" height="5" fill="#232323"/></svg>
  <div class="contact" style="top:365px">www.profilenet.example/marcusthalberg</div>

  <div class="divider" style="left:58px;top:389px;width:170px"></div>
  <div class="side-title" style="left:32px;top:395px">QUALIFICATIONS</div>
  <div class="divider" style="left:58px;top:418px;width:170px"></div>

  <div class="side-line" style="top:434px;height:340px"></div>
  <div class="side-head" style="top:431px">CORE COMPETENCIES</div>
  <div class="side-item" style="top:451px">Passionate Digital Transformation<br>Leader with track record of launching<br>and growing business</div>
  <div class="side-item" style="top:492px">Entrepreneurial background with<br>network to global innovation hubs</div>
  <div class="side-item" style="top:522px">Strong Product &amp; Innovation<br>competence with a clear<br>understanding of market needs</div>
  <div class="side-item" style="top:562px">Track record in driving<br>partnerships into highly successful<br>collaborations</div>
  <div class="side-head" style="top:616px">ACCOMPLISHMENTS</div>
  <div class="side-item" style="top:638px">Mentor at Chipworks' Launch program<br>for start-ups</div>
  <div class="side-item" style="top:668px">Crash Course in Data Science at<br>Harbor State University</div>
  <div class="side-item" style="top:698px">Intro to Blockchain Technology at<br>Westbridge School</div>
  <div class="side-item" style="top:728px">PSM 1, Certified Scrum Master,<br>Agile Guild</div>
  <div class="side-item" style="top:758px">Leadership Excellence Program<br>at Meridian Business School</div>

  <div class="banner" style="left:287px;top:31px">PROFILE &amp; ACHIEVEMENTS</div>
  <div class="timeline" style="left:296px;top:70px;height:330px"></div>
  <div class="r-head dot" style="left:309px;top:70px">GUIDING ENTREPRENEURIAL INNOVATIONS</div>
  <div class="r-item" style="left:321px;top:88px">Define a way forward for Corvanta's Messaging business</div>
  <div class="r-item" style="left:321px;top:108px">Shape a venture for Voltrix in the eMobilty segment</div>
  <div class="r-item" style="left:321px;top:128px">Build a joint venture of Nordtel Group and Optivo for the<br>development of connected smart glasses</div>
  <div class="r-head dot" style="left:309px;top:159px">LEADING GLOBAL PARTNERSHIP NETWORKS</div>
  <div class="r-item" style="left:321px;top:179px">Overcome strategic objectives and form an alliance of<br>Searchly and Corvanta in Messaging</div>
  <div class="r-item" style="left:321px;top:209px">Position Nordtel Group as first choice for Orchard<br>smartphones with a purchase volume of more than 2<br>billion euro</div>
  <div class="r-item" style="left:321px;top:249px">Create exclusive advantages for Nordtel Group<br>customers through partnerships with major innovators<br>like Orchard and Riverstone</div>
  <div class="r-head dot" style="left:309px;top:290px">GUIDING ENTREPRENEURIAL INNOVATIONS</div>
  <div class="r-item" style="left:321px;top:307px">Manage the roll out of new GSM-R Units to &gt;5000 vehicles<br>for Federal Rail AG in logistics and technical integration</div>
  <div class="r-item" style="left:321px;top:337px">Open the door for IoT business of Quadrant to access<br>European telcos</div>
  <div class="r-item" style="left:321px;top:367px">Develop a consistent Home@plus experience and<br>build the corresponding device portfolio supporting DSL, TV,<br>Smart Home</div>

  <div class="banner" style="left:287px;top:410px">EXPERIENCE <span class="light">(EXEMPLARY)</span></div>
  <div class="timeline" style="left:296px;top:452px;height:400px"></div>
  <div class="r-head dot" style="left:309px;top:452px">SENIOR ADVISOR (SELF-EMPLOYED)</div>
  <div class="job" style="left:309px;width:272px;top:474px"><span>Launchbay Corporate Startups</span><span class="date">10/2020 – Present</span></div>
  <div class="r-item" style="left:321px;top:496px">Venture building (e.g. with Voltrix and NT)</div>
  <div class="r-item" style="left:321px;top:516px">Derive a product strategy and go to market plan<br>Key Success:</div>
  <div class="r-item" style="left:321px;top:546px">Successful start of Voltgo, the Voltrix eMobility venture</div>
  <div class="job" style="left:309px;width:272px;top:565px"><span>Quadrant Communications</span><span class="date">08/2021 – Present</span></div>
  <div class="r-item" style="left:321px;top:587px">Define a strategy how to approach telco carriers</div>
  <div class="r-item" style="left:321px;top:607px">Evaluate business models to engage with distributors<br>Key Success:</div>
  <div class="r-item" style="left:321px;top:637px">Growth through new distribution channels via carriers</div>
  <div class="job" style="left:309px;width:272px;top:660px"><span>Corvanta</span><span class="date">04/2021 – 04/2022</span></div>
  <div class="r-item" style="left:321px;top:681px">Evaluation of the global messaging business</div>
  <div class="r-item" style="left:321px;top:701px">Define a new strategy for messaging in Corvanta</div>
  <div class="r-item" style="left:321px;top:721px">Implement a new independent business unit for SaaS<br>Key Success:</div>
  <div class="r-item" style="left:321px;top:751px">Successful start of the new business unit</div>
  <div class="job" style="left:309px;width:272px;top:777px"><span>Northpoint Consulting</span><span class="date">10/2020 – 12/2022</span></div>
  <div class="r-item" style="left:321px;top:799px">Steering of a group wide exchange of GSM-R equipment<br>Key Success:</div>
  <div class="r-item" style="left:321px;top:829px">Improvement of the mobile connectivity experience for<br>customers of the Federal Rail AG</div>
</main>

<main class="page page-two">
  <div class="band"></div>
  <svg class="shape" viewBox="0 0 628 886" aria-hidden="true">
    <path d="M31,72 Q31,50 53,50 H232 Q254,50 254,72 V450 L156,548 H53 Q31,548 31,526 Z" fill="#232323"/>
    <path d="M254,450 C244,490 200,528 156,548 C178,515 186,497 192,480 C212,474 236,466 254,450 Z" fill="#8c8c8c" role="img" aria-label="Folded page corner"/>
  </svg>

  <div class="divider" style="left:58px;top:81px;width:166px"></div>
  <div class="side-title" style="left:30px;top:86px">UNIVERSITY</div>
  <div class="divider" style="left:58px;top:107px;width:166px"></div>
  <div class="side-text" style="top:125px">Executive Leadership Development<br>Program at Crestview Graduate<br>School of Business (2016)</div>
  <div class="side-text" style="top:166px">Diploma in Electrical Engineering at<br>Technical University Rhineland<br>(TUR) (1987-1994)</div>

  <div class="divider" style="left:58px;top:229px;width:166px"></div>
  <div class="side-title" style="left:30px;top:234px">ACTIVITIES</div>
  <div class="divider" style="left:58px;top:255px;width:166px"></div>
  <div class="side-text" style="top:275px;width:60px">German</div>
  <div class="side-text" style="left:138px;top:275px;width:90px">Native</div>
  <div class="side-text" style="top:295px;width:60px">English</div>
  <div class="side-text" style="left:138px;top:295px;width:90px">Full professional<br>proficiency</div>

  <div class="divider" style="left:58px;top:344px;width:166px"></div>
  <div class="side-title" style="left:30px;top:349px">REFERENCES</div>
  <div class="divider" style="left:58px;top:370px;width:166px"></div>
  <div class="side-text" style="top:387px">Tobias Hellmann, CEO Nordtel<br>Group</div>
  <div class="side-text" style="top:417px">Martin Haller, SVP Global<br>Strategic Projects and Marketing<br>Partnerships, Nordtel Group</div>
  <div class="side-text" style="top:458px">Yannick Morel, formerly CEO<br>Brightwave Corporation</div>

  <div class="banner" style="left:286px;top:52px">EXPERIENCE <span class="light">(EXEMPLARY)</span></div>
  <div class="timeline" style="left:298px;top:96px;height:452px"></div>
  <div class="r-head dot" style="left:308px;top:95px">NORDTEL GROUP AG, BONN</div>
  <div class="job" style="left:308px;width:273px;top:120px"><span>Senior Vice President Connected<br>Devices</span><span class="date">08/2011 – 07/2020</span></div>
  <div class="r-item" style="left:320px;top:152px">Management of the global partnerships with Orchard,<br>Searchly, Solaro</div>
  <div class="r-item" style="left:320px;top:182px">Board member of Lensa Inc, a JV of NT and Optivo AG</div>
  <div class="r-item" style="left:320px;top:203px">Driving the entire portfolio of devices for the NT group<br>including Wearables, Voice Controlled Devices and<br>Virtual Reality Glasses</div>
  <div class="r-sub" style="left:308px;top:251px">Key Successes</div>
  <div class="r-item" style="left:320px;top:271px">Managing a turnover of more than 3 billion euros with<br>devices across the Nordtel Group</div>
  <div class="r-item" style="left:320px;top:302px">Development of the first Home@plus Voice Speaker</div>
  <div class="r-item" style="left:320px;top:322px">Foundation of the Lensa joint venture</div>
  <div class="job" style="left:308px;width:273px;top:351px"><span>Vice President Product<br>Management Mobile</span><span class="date">08/2011 – 07/2020</span></div>
  <div class="r-item" style="left:320px;top:388px">Introduction of the international portfolio of mobile<br>phones in Nordtel Group</div>
  <div class="r-item" style="left:320px;top:418px">Project lead for key initiatives, e.g. introduction<br>of Andromo</div>
  <div class="r-sub" style="left:308px;top:459px">Key Successes</div>
  <div class="r-item" style="left:320px;top:481px">Successful introduction of the first Andromo phone in<br>an exclusive partnership with Searchly and Brightwave</div>
  <div class="r-item" style="left:320px;top:511px">Development of the NT App portfolio for Pomme OS<br>and Andromo</div>

  <div class="banner" style="left:165px;top:580px">EXPERIENCE <span class="light">(EXEMPLARY)</span></div>
  <div class="r-head" style="left:0;width:628px;top:633px;text-align:center">NORDTEL MOBILE INTERNATIONAL, BONN</div>

  <div class="job" style="left:42px;width:232px;top:660px"><span>Head of Client Integration<br>ISP Products</span><span class="date">08/2011 – 07/2020</span></div>
  <div class="r-item" style="left:54px;top:694px">Conception and development of a<br>NT-branded mobile phone</div>
  <div class="r-item" style="left:54px;top:724px">Transformation of product management<br>from voice-centric into mobile internet<br>business</div>

  <div class="job" style="left:322px;width:259px;top:660px"><span>Project Lead Personal<br>Communication Services</span><span class="date">08/2011 – 07/2020</span></div>
  <div class="r-item" style="left:333px;top:694px">Project lead of the first FMC product combining<br>fixed and mobile communication on one bill<br>with one device and one service</div>

  <div class="job" style="left:209px;width:209px;top:765px;gap:12px;justify-content:flex-start"><span>Project Engineering</span><span class="date">08/2011 – 07/2020</span></div>
  <div class="r-item" style="left:54px;top:794px">Project lead "Short Message<br>Service Center"</div>
  <div class="r-item" style="left:209px;top:794px">Audits of system technology<br>suppliers</div>
  <div class="r-item" style="left:361px;top:794px">Voice quality assurance: Design of a new<br>measurement system and implementation in C++</div>
</main>

</body>
</html>
```